Business Cards - Brightpath Horizon

need to design unique business card for my mortgage business. I need to design credit card style business card for my business or any unique idea that you might have

Target Market(s)

Home Loan customers

Industry/Entity Type

Mortgage Brokerage

Contact Information for Business Card

please design credit card style or very unique style business card

Colors

Designer to choose colors to be used in the design.

Requirements
Must have
• Name
• position
• Phone number
• fax number
• email address
• website address
• social media address
• All above fields will be provided once design in finalised

```html
<!DOCTYPE html>
<html lang="en">
<head>
<meta charset="utf-8">
<title>Brightpath Horizon – Business Cards</title>
<link rel="stylesheet" href="https://fonts.googleapis.com/css2?family=Cinzel:wght@700&family=Open+Sans:wght@400&display=swap">
<style>
  :root {
    --backdrop: #e9e4dc;
    --card: #050505;
    --card-edge: #1a1a1a;
    --brand-blue: #1f4fd6;
    --brand-grey: #5c5c5c;
    --accent-orange: #f08a16;
    --text-light: #d9d9d9;
    --social: #3d6fa8;
  }
  * { margin: 0; padding: 0; box-sizing: border-box; }
  html, body { width: 1200px; height: 900px; overflow: hidden; }
  body {
    background: var(--backdrop);
    position: relative;
    font-family: "Open Sans", Arial, sans-serif;
  }
  .card {
    position: absolute;
    left: 290px;
    width: 620px;
    height: 354px;
    background: var(--card);
    border: 1px solid var(--card-edge);
    border-radius: 4px;
    box-shadow: 0 10px 24px rgba(0,0,0,0.25);
    overflow: hidden;
  }
  .card--back { top: 66px; }
  .card--front { top: 480px; }

  .brand-name {
    font-family: "Cinzel", Georgia, serif;
    font-weight: 700;
    letter-spacing: 1px;
    white-space: nowrap;
  }

  /* back */
  .back-brand {
    position: absolute;
    left: 0; right: 0; top: 150px;
    text-align: center;
  }
  .back-brand .brand-name { font-size: 42px; color: var(--brand-grey); }

  /* front */
  .front-brand {
    position: absolute;
    left: 58px; top: 66px;
  }
  .front-brand .brand-name { font-size: 32px; color: var(--brand-blue); }

  .tree-shade {
    position: absolute;
    right: 0; top: 0;
    width: 230px; height: 250px;
    background: radial-gradient(ellipse at 50% 40%, #161616 0%, #0c0c0c 55%, var(--card) 80%);
  }

  .holder {
    position: absolute;
    left: 58px; top: 176px;
  }
  .holder-name {
    font-family: "Cinzel", Georgia, serif;
    font-weight: 700;
    font-size: 22px;
    color: var(--accent-orange);
    letter-spacing: 0.5px;
  }
  .holder-role { font-size: 15px; color: var(--text-light); margin-top: -2px; }

  .contact-list {
    position: absolute;
    left: 58px; top: 242px;
    list-style: none;
  }
  .contact-list li {
    display: flex;
    align-items: center;
    gap: 10px;
    font-size: 15px;
    color: var(--text-light);
    height: 24px;
  }
  .contact-list svg { width: 14px; height: 14px; flex: none; fill: var(--accent-orange); }

  .social-links {
    position: absolute;
    right: 24px; top: 226px;
    display: flex;
    gap: 4px;
  }
  .social-links span {
    width: 22px; height: 22px;
    background: var(--social);
    border-radius: 2px;
  }
</style>
</head>
<body>

<section class="card card--back" aria-label="Business card back">
  <div class="back-brand">
    <div class="brand-name">BRIGHTPATH HORIZON</div>
  </div>
</section>

<section class="card card--front" aria-label="Business card front">
  <div class="tree-shade" role="img" aria-label="Faint dark tree silhouette decoration"></div>

  <div class="front-brand">
    <div class="brand-name">BRIGHTPATH HORIZON</div>
  </div>

  <div class="holder">
    <div class="holder-name">MARCUS ELLWOOD</div>
    <div class="holder-role">Managing Director</div>
  </div>

  <ul class="contact-list">
    <li>
      <svg viewBox="0 0 16 16" aria-hidden="true"><path d="M1 5c0-2 3-3 7-3s7 1 7 3v1.5h-3.5V5H4.5v1.5H1z M3 8h10l1 6H2z"/></svg>
      (044)555019283
    </li>
    <li>
      <svg viewBox="0 0 16 16" aria-hidden="true"><path d="M4 1h6l2 2v3h2v9H2V6h2z M5 2.5V6h5.5V3.5L9.5 2.5z M5 9h6v1H5z M5 11.5h6v1H5z"/></svg>
      (044)555019284
    </li>
    <li>
      <svg viewBox="0 0 16 16" aria-hidden="true"><path d="M1 3h14v10H1z M2.5 4.5v.4L8 9l5.5-4.1v-.4z"/></svg>
      info@brightpathmail.com
    </li>
    <li>
      <svg viewBox="0 0 16 16" aria-hidden="true"><path d="M8 1a7 7 0 1 0 0 14A7 7 0 0 0 8 1z M8 3a5 5 0 0 1 4.6 3H9.5L8 4.5 6.5 7 4 8.5l2 2.5h2.5l.5 2A5 5 0 0 1 8 3z"/></svg>
      www.brightpathhorizon.com
    </li>
  </ul>

  <div class="social-links" aria-label="Social media links">
    <span></span><span></span><span></span>
  </div>
</section>

</body>
</html>
```